Yacht, Boats, Watersports company needs a redesign of business card

Hello Designers!
We are a Boat dealership company that sells fun in the water, we sell boats, Yachts, Kayaks and also yacht WaterSport toys. We are looking to redesign our business cards in to something a little bit more sophisticated. in a way that we can make better use of our company colors. I'm attaching a zipped file containing the company 3 sets of company logo which one is an horizontal another one is a vertical and also a chromed 3d logo. Also is included two set of business cards that we use and also some designs that i think it's interesting. We use PMS 2026c Orange and PMS 7687C Blue. I would like to see at least two different options with the orange as accent and also using blue as an accent color. It's really important for the business cards to have a font option and size that is legible to most people. Our current website is wwww.coralpennant.com. Please visit if you want to have a better feeling of the Boat dealership
You can send Single sided or double side options. We are now using single sided but we may be open for a double side option if we really like the design.
Target Market(s)
Marine, boat sales, yacht sales, water toys sales/
Contact Information for Business Card
Name: Dale Whitcombe
Address: 212 North Fenwick Lane,
Palm Cove, FL 33071
Phone: 954-731-8842
Fax: 954:731-8843
Cell: 954-382-1490
Email: dw@coralpennant.com
Website: coralpennant.com
Requirements
Must have
- the current information of the business card provided.
logo
use the PMS Colors
Nice to have
- a touch of elegance and sophistication but simple
Should not have
- should not have any typography that is hard to read, the card should be simple but yet sophisticated.

```html
<!DOCTYPE html>
<html lang="en">
<head>
<meta charset="utf-8">
<title>Coral Pennant – Business Card</title>
<link href="https://fonts.googleapis.com/css2?family=Montserrat:wght@300;500;700&display=swap" rel="stylesheet">
<style>
  :root {
    --orange: #e2643a;
    --blue: #1f4c7e;
    --white: #f3f3f3;
    --stage: #1e1e20;
  }
  html, body { margin: 0; padding: 0; overflow: hidden; }
  body {
    width: 1200px; height: 1000px;
    background: var(--stage);
    font-family: "Montserrat", sans-serif;
    position: relative;
  }
  .card {
    position: absolute; top: 168px;
    width: 380px; height: 664px;
    background: var(--orange);
    border-radius: 26px;
    box-sizing: border-box;
    padding: 22px;
  }
  .card--front { left: 170px; }
  .card--back  { left: 650px; }

  .card__panel {
    position: relative;
    width: 100%; height: 100%;
    background: var(--blue);
    border-radius: 30px;
    overflow: hidden;
  }

  /* Front */
  .brand-mark {
    position: absolute; left: 50%; top: 70px;
    width: 170px; height: 170px;
    transform: translateX(-50%);
    border: 14px solid var(--orange);
    border-radius: 50%;
    box-sizing: border-box;
  }
  .brand-name {
    position: absolute; left: 0; right: 0; top: 268px;
    text-align: center;
    color: var(--white);
    font-weight: 700; font-size: 27px; letter-spacing: 2px;
    text-transform: uppercase;
  }
  .name-band {
    position: absolute; left: 0; right: 0; top: 390px;
    height: 96px;
    background: var(--orange);
    display: flex; align-items: center; justify-content: center;
  }
  .name-band__name {
    color: var(--blue);
    font-weight: 700; font-size: 30px; letter-spacing: 0.5px;
    text-transform: uppercase;
  }

  /* Back */
  .address {
    position: absolute; left: 34px; top: 44px;
    color: var(--white);
    font-weight: 300; font-size: 20px; line-height: 28px;
  }
  .icon-row {
    position: absolute; left: 50%; transform: translateX(-50%);
  }
  .icon-row--web { top: 142px; }
  .icon-row--phones { top: 358px; }
  .numbers {
    position: absolute; left: 0; right: 0; top: 196px;
    text-align: center;
    color: var(--white);
    font-weight: 700; font-size: 22px; line-height: 38px; letter-spacing: 2px;
  }
  .links {
    position: absolute; left: 0; right: 0; top: 410px;
    text-align: center;
    color: var(--white);
    font-weight: 500; font-size: 19px; line-height: 30px;
  }
  .links__accent { color: var(--orange); }
  .back-brand {
    position: absolute; left: 0; right: 0; bottom: 40px;
    display: flex; align-items: center; justify-content: center; gap: 14px;
  }
  .back-brand__mark {
    width: 54px; height: 54px;
    border: 7px solid var(--orange);
    border-radius: 50%;
    box-sizing: border-box;
  }
  .back-brand__name {
    color: var(--white);
    font-weight: 700; font-size: 22px; letter-spacing: 1.5px;
    text-transform: uppercase; line-height: 26px;
  }
</style>
</head>
<body>

<section class="card card--front" aria-label="Card front">
  <div class="card__panel">
    <div class="brand-mark"></div>
    <div class="brand-name">Coral Pennant</div>
    <div class="name-band">
      <span class="name-band__name">Dale Whitcombe</span>
    </div>
  </div>
</section>

<section class="card card--back" aria-label="Card back">
  <div class="card__panel">
    <div class="address">212 North Fenwick Lane,<br>Palm Cove, FL 33071</div>

    <svg class="icon-row icon-row--web" width="82" height="34" viewBox="0 0 82 34" aria-label="Email and web icons">
      <line x1="17" y1="17" x2="65" y2="17" stroke="var(--orange)" stroke-width="3"/>
      <circle cx="17" cy="17" r="15" fill="var(--orange)"/>
      <circle cx="65" cy="17" r="15" fill="var(--orange)"/>
      <rect x="9" y="11" width="16" height="12" fill="none" stroke="var(--white)" stroke-width="2"/>
      <path d="M9 11 l8 7 8 -7" fill="none" stroke="var(--white)" stroke-width="2"/>
      <circle cx="65" cy="17" r="8" fill="none" stroke="var(--white)" stroke-width="2"/>
      <line x1="57" y1="17" x2="73" y2="17" stroke="var(--white)" stroke-width="1.5"/>
      <ellipse cx="65" cy="17" rx="3.5" ry="8" fill="none" stroke="var(--white)" stroke-width="1.5"/>
    </svg>

    <div class="numbers">
      954-731-8842<br>954-382-1490<br>954:731-8843
    </div>

    <svg class="icon-row icon-row--phones" width="130" height="34" viewBox="0 0 130 34" aria-label="Phone, cell and fax icons">
      <line x1="17" y1="17" x2="113" y2="17" stroke="var(--orange)" stroke-width="3"/>
      <circle cx="17" cy="17" r="15" fill="var(--orange)"/>
      <circle cx="65" cy="17" r="15" fill="var(--orange)"/>
      <circle cx="113" cy="17" r="15" fill="var(--orange)"/>
      <path d="M11 10 q-2 8 8 14 l3 -3 -3 -3 -2 1 q-3 -2 -4 -5 l2 -1 -1 -4 z" fill="var(--white)"/>
      <rect x="60" y="8" width="10" height="18" rx="2" fill="none" stroke="var(--white)" stroke-width="2"/>
      <rect x="105" y="12" width="16" height="11" rx="1" fill="var(--white)"/>
      <rect x="108" y="7" width="10" height="5" fill="var(--white)"/>
    </svg>

    <div class="links">
      dw@<span class="links__accent">coralpennant</span>.com<br>
      www.<span class="links__accent">coralpennant</span>.com
    </div>

    <div class="back-brand">
      <div class="back-brand__mark"></div>
      <div class="back-brand__name">Coral<br>Pennant</div>
    </div>
  </div>
</section>

</body>
</html>
```